Teach English in China Website Redesign Needed

We recruit native English speakers from the US, UK, etc. who want to teach English as a foreign language in schools in China. Our target customer is college educated, age 22-28 and they love to travel. We prefer designs with bright colors and lots of photos. We want to keep all the text on our current homepage, BrightLanternPost.com. We are open to changing our logo. A competitor's page that we like is pinemeadowtutors.com because of their bright colors, photos and use of white space. We are happy to give you a dofollow link and design credit on our homepage. The use of included photos is optional. We need at least a home page design and a standard blog post design.
Target Market(s)
Our target customer is college educated, age 22-28 and they love to travel. Half of our customers are kindergarten teachers. Half of our customers are male.
Logo Text
Bright Lantern Post
Requirements
Must have
- Bright colors
Should not have
- Our homepage must not look crowded. Use white space effectively.

```html
<!DOCTYPE html>
<html lang="en">
<head>
<meta charset="utf-8">
<title>Bright Lantern Post – Teach English in China</title>
<link href="https://fonts.googleapis.com/css2?family=Raleway:wght@500;600;700;800&family=Open+Sans:ital,wght@0,400;0,600;0,700;1,400&display=swap" rel="stylesheet">
<style>
:root{
  --red:#e2001a;
  --ink:#1f1f1f;
  --text:#555;
  --muted:#888;
  --line:#e3e3e3;
  --soft:#f4f4f4;
  --footer:#161616;
  --white:#fff;
}
*{box-sizing:border-box;margin:0;padding:0}
html,body{width:1200px;height:4306px;overflow:hidden}
body{font-family:"Open Sans",Arial,sans-serif;color:var(--text);background:var(--white);font-size:13px;line-height:1.6}
h1,h2,h3,h4,.brand{font-family:"Raleway",Arial,sans-serif}
.wrap{width:880px;margin:0 auto;position:relative}
.section-title{font-family:"Raleway",Arial,sans-serif;font-weight:800;font-size:23px;color:var(--ink);text-align:center;letter-spacing:.5px;text-transform:uppercase}
.section-title span{color:var(--red)}
.btn{display:inline-block;background:var(--red);color:var(--white);font-family:"Raleway",Arial,sans-serif;font-weight:700;font-size:13px;text-transform:uppercase;padding:11px 20px;border-radius:2px;letter-spacing:.4px}

/* top bar */
.topbar{height:24px;background:var(--ink);color:#bbb;font-size:10px}
.topbar .wrap{display:flex;justify-content:space-between;align-items:center;height:24px}
.topbar nav a{margin-right:14px}
.social{display:flex;gap:12px}
.social i{display:block;width:9px;height:9px;border-radius:50%;background:#ccc}

/* header */
.header{height:94px;border-bottom:1px solid var(--line)}
.header .wrap{display:flex;justify-content:space-between;align-items:center;height:94px}
.brand{font-weight:800;font-size:26px;color:var(--ink);display:flex;align-items:center;gap:10px;line-height:1}
.brand .dot{width:14px;height:14px;border-radius:50%;background:var(--red)}
.mainnav{display:flex;gap:40px;align-items:center;font-family:"Raleway",Arial,sans-serif;font-weight:700;font-size:13px;color:var(--ink)}
.mainnav .active{color:var(--red)}

/* hero */
.hero{height:517px;position:relative;background:radial-gradient(ellipse at 38% 55%,#c2661f 0%,#6a2a10 22%,#22150f 50%,#0c0a08 80%)}
.hero .arrow{position:absolute;top:236px;width:40px;height:40px;border-radius:50%;background:rgba(255,255,255,.15);display:flex;align-items:center;justify-content:center}
.hero .arrow.prev{left:26px}.hero .arrow.next{right:26px}
.side-tabs{position:absolute;right:0;top:118px;width:108px}
.side-tabs span{display:block;text-align:center;color:var(--white);font-family:"Raleway",Arial,sans-serif;font-weight:700;font-size:12px;padding:8px 0;text-transform:uppercase}
.side-tabs .board{background:#111}
.side-tabs .apply{background:var(--red)}

/* jobs */
.jobs{height:660px;padding-top:42px}
.job-grid{display:grid;grid-template-columns:repeat(3,272px);column-gap:32px;row-gap:40px;margin-top:36px}
.job-card{text-align:center}
.job-card .photo{height:152px}
.job-card h3{color:var(--red);font-weight:700;font-size:17px;margin:14px 0 6px}
.job-card p{font-size:11px;line-height:1.55;padding:0 14px}

/* highlights */
.highlights{height:347px;background:linear-gradient(180deg,#7fa3c4 0%,#b8cde0 45%,#d7e1ea 70%,#8e9caa 100%);position:relative}
.highlights .wrap{padding-top:70px}
.highlights h2{font-weight:800;font-size:25px;color:var(--ink);text-transform:uppercase;margin-bottom:10px}
.highlights ul{list-style:none;font-size:13px;color:var(--ink)}
.highlights li{line-height:1.85}
.highlights li::before{content:"•";margin-right:8px}
.highlights .btn{margin-top:14px}

/* testimonials */
.testimonials{height:440px;padding-top:48px;position:relative}
.t-grid{display:grid;grid-template-columns:repeat(4,206px);gap:19px;margin-top:32px}
.t-card{border:1px solid var(--line);height:250px;text-align:center;padding:22px 16px 0;position:relative}
.avatar{width:72px;height:72px;border-radius:50%;margin:0 auto}
.stars{color:var(--red);font-size:14px;letter-spacing:1px;margin:10px 0 6px}
.t-card p{font-size:11px;font-style:italic;line-height:1.5}
.t-card .name{position:absolute;left:50%;bottom:14px;transform:translateX(-50%);background:#c8c8c8;color:var(--white);font-size:10px;padding:3px 16px;border-radius:10px;white-space:nowrap}
.shadow-rule{position:absolute;left:50%;bottom:0;width:880px;transform:translateX(-50%);height:12px;background:radial-gradient(ellipse at top,rgba(0,0,0,.12),transparent 70%)}

/* locations */
.locations{height:553px;padding-top:66px}
.loc-body{display:flex;gap:24px;margin-top:44px}
.loc-grid{display:grid;grid-template-columns:272px 272px;gap:20px 20px;width:564px}
.loc-tile{height:160px;position:relative}
.loc-tile span{position:absolute;left:0;right:0;bottom:20px;text-align:center;color:var(--white);font-family:"Raleway",Arial,sans-serif;font-weight:600;font-size:17px}
.loc-side{width:292px;font-size:12px}
.loc-side .map{height:250px;margin-top:20px;background:linear-gradient(135deg,#f7f7f7,#e4e4e4);border-radius:4px}

/* how it works */
.how{height:436px;background:var(--soft);padding-top:60px}
.steps{display:grid;grid-template-columns:repeat(4,190px);gap:40px;margin-top:40px;text-align:center}
.step .circle{width:110px;height:110px;border-radius:50%;border:3px solid var(--ink);background:var(--white);margin:0 auto;display:flex;align-items:center;justify-content:center}
.step h3{color:var(--red);font-weight:700;font-size:17px;margin:14px 0 6px}
.step p{font-size:11px;line-height:1.55}

/* blog */
.blog{height:551px;padding-top:56px;position:relative}
.posts{display:grid;grid-template-columns:repeat(2,420px);column-gap:40px;row-gap:40px;margin-top:44px}
.post{display:flex;gap:16px}
.post .thumb{width:184px;height:150px;flex:none}
.post h3{color:var(--red);font-weight:700;font-size:16px;margin-bottom:6px;line-height:1.3}
.post p{font-size:11px;line-height:1.6}
.post .date{font-size:10px;color:var(--muted);margin-top:8px;display:flex;align-items:center;gap:5px}

/* job board banner */
.banner{height:340px;background:linear-gradient(90deg,#d9dfe4 0%,#cfd6dc 45%,#b9c2ca 70%,#8f8070 100%);position:relative}
.banner .wrap{padding-top:108px}
.banner h2{font-weight:800;font-size:25px;color:var(--ink);text-transform:uppercase}
.banner p{font-size:13px;color:var(--ink);margin:8px 0 14px;width:340px}

/* footer */
.footer{height:344px;background:var(--footer);color:#bbb;border-top:3px solid var(--red);position:relative}
.f-cols{display:grid;grid-template-columns:225px 240px 215px 200px;padding-top:40px}
.f-cols h4{color:var(--white);font-size:12px;font-weight:700;text-transform:uppercase;margin-bottom:14px}
.f-cols ul{list-style:none;font-size:10.5px}
.f-cols li{line-height:2.2}
.f-cols li::before{content:"›";margin-right:8px;color:var(--muted)}
.contact li::before{content:none}
.contact li{display:flex;gap:8px;line-height:1.7;margin-bottom:6px}
.contact svg{flex:none;margin-top:3px}
.f-bottom{position:absolute;left:0;right:0;bottom:22px}
.f-bottom .wrap{display:flex;justify-content:space-between;align-items:center;font-size:10px}
.f-bottom .brand{font-size:19px;color:var(--white)}
.live-chat{position:absolute;right:0;top:176px;width:28px;height:84px;background:var(--red);color:var(--white);font-size:9px;font-weight:700;writing-mode:vertical-rl;transform:rotate(180deg);text-align:center;line-height:28px}
</style>
</head>
<body>

<div class="topbar">
  <div class="wrap">
    <nav><a>Job Board</a><a>Apply</a><a>Blog</a><a>Hire a Teacher</a><a>About Us</a></nav>
    <div class="social"><i></i><i></i><i></i><i></i><i></i><i></i></div>
  </div>
</div>

<header class="header">
  <div class="wrap">
    <div class="brand"><span class="dot"></span>Bright Lantern Post</div>
    <nav class="mainnav">
      <a class="active">HOME</a><a>AVAILABLE JOBS</a><a>APPLY ONLINE</a><a>BLOG</a><a>FAQ</a>
      <svg width="14" height="14" viewBox="0 0 14 14"><circle cx="6" cy="6" r="4.5" fill="none" stroke="#e2001a" stroke-width="2"/><line x1="9.5" y1="9.5" x2="13" y2="13" stroke="#e2001a" stroke-width="2"/></svg>
    </nav>
  </div>
</header>

<section class="hero" role="img" aria-label="Photo of a fisherman with a straw hat holding a glowing lantern at night">
  <span class="arrow prev"><svg width="12" height="12" viewBox="0 0 12 12"><path d="M8 1 3 6l5 5" fill="none" stroke="#fff" stroke-width="2"/></svg></span>
  <span class="arrow next"><svg width="12" height="12" viewBox="0 0 12 12"><path d="M4 1l5 5-5 5" fill="none" stroke="#fff" stroke-width="2"/></svg></span>
  <div class="side-tabs"><span class="board">Job Board</span><span class="apply">Apply Now</span></div>
</section>

<section class="jobs">
  <div class="wrap">
    <h2 class="section-title">Teaching Jobs <span>in China</span></h2>
    <div class="job-grid">
      <article class="job-card"><div class="photo" role="img" aria-label="Photo of schoolchildren in red scarves in a classroom" style="background:linear-gradient(135deg,#d9d3cc,#b84a3e)"></div><h3>Finibus Bonorum</h3><p>Sed ut perspiciatis unde omnis iste natusit volupta tem accusantium doloremque laudantotam.</p></article>
      <article class="job-card"><div class="photo" role="img" aria-label="Photo of a young child eating noodles with chopsticks" style="background:linear-gradient(135deg,#e6dcd2,#b79a86)"></div><h3>Finibus Bonorum</h3><p>Sed ut perspiciatis unde omnis iste natusit volupta tem accusantium doloremque laudantotam.</p></article>
      <article class="job-card"><div class="photo" role="img" aria-label="Photo of kindergarten children playing outdoors" style="background:linear-gradient(135deg,#e7d9b2,#c9a23d)"></div><h3>Finibus Bonorum</h3><p>Sed ut perspiciatis unde omnis iste natusit volupta tem accusantium doloremque laudantotam.</p></article>
      <article class="job-card"><div class="photo" role="img" aria-label="Photo of children at desks in a bright classroom" style="background:linear-gradient(135deg,#d8b9b2,#b8312c)"></div><h3>Finibus Bonorum</h3><p>Sed ut perspiciatis unde omnis iste natusit volupta tem accusantium doloremque laudantotam.</p></article>
      <article class="job-card"><div class="photo" role="img" aria-label="Photo of pupils in uniforms lined up in a schoolyard" style="background:linear-gradient(135deg,#7a6a68,#9a2b30)"></div><h3>Finibus Bonorum</h3><p>Sed ut perspiciatis unde omnis iste natusit volupta tem accusantium doloremque laudantotam.</p></article>
      <article class="job-card"><div class="photo" role="img" aria-label="Photo of a small child in a red jacket eating noodles" style="background:linear-gradient(135deg,#e0d4c6,#c23a2a)"></div><h3>Finibus Bonorum</h3><p>Sed ut perspiciatis unde omnis iste natusit volupta tem accusantium doloremque laudantotam.</p></article>
    </div>
  </div>
</section>

<section class="highlights" role="img" aria-label="Photo of the Shanghai skyline with the TV tower under a blue sky">
  <div class="wrap">
    <h2>Highlights</h2>
    <ul>
      <li>5000 RMB at end of completed 1 year contract</li>
      <li>Free TESOL / TEFL training and certification</li>
      <li>Invitation letter so you can apply for a visa</li>
      <li>Airport pickup</li>
      <li>Free Chinese classes 2 hours per week with most jobs</li>
    </ul>
    <span class="btn">View More</span>
  </div>
</section>

<section class="testimonials">
  <div class="wrap">
    <h2 class="section-title">Client <span>Testimonials</span></h2>
    <div class="t-grid">
      <div class="t-card"><div class="avatar" role="img" aria-label="Portrait photo of a client" style="background:#4a3a36"></div><div class="stars">★★★★★</div><p>Marla was extremely helpful during the entire process. Moving to another country is a very challenging stride!</p><span class="name">Owen Hartley</span></div>
      <div class="t-card"><div class="avatar" role="img" aria-label="Portrait photo of a client" style="background:#8a8f86"></div><div class="stars">★★★★★</div><p>When I began my search for a teaching job in China, I had no idea what to expect. Luckily, I came across Marla with English</p><span class="name">Clara Winslow</span></div>
      <div class="t-card"><div class="avatar" role="img" aria-label="Portrait photo of a client" style="background:#6b4a46"></div><div class="stars">★★★★★</div><p>As soon as we got in touch, Marla guided me through every step of the process. I have had THE BEST experience under her guidance.</p><span class="name">Dana Whitfield</span></div>
      <div class="t-card"><div class="avatar" role="img" aria-label="Portrait photo of a client" style="background:#3a2b30"></div><div class="stars">★★★★★</div><p>All of this was only what she did during the search process! She even continued to guide and comfort me when and after I arrived in China.</p><span class="name">Ben Carver</span></div>
    </div>
  </div>
  <div class="shadow-rule"></div>
</section>

<section class="locations">
  <div class="wrap">
    <h2 class="section-title">Locations to Teach <span>English in China</span></h2>
    <div class="loc-body">
      <div class="loc-grid">
        <div class="loc-tile" role="img" aria-label="Photo of a traditional red pagoda against a blue sky" style="background:linear-gradient(180deg,#4d79b8,#8c2d22)"><span>Finibus Bonorum</span></div>
        <div class="loc-tile" role="img" aria-label="Photo of a city skyline with high-rise towers" style="background:linear-gradient(180deg,#7fa3c9,#3f4a58)"><span>Finibus Bonorum</span></div>
        <div class="loc-tile" role="img" aria-label="Photo of the Pudong skyline at dusk" style="background:linear-gradient(180deg,#6d96c8,#2f3c4c)"><span>Finibus Bonorum</span></div>
        <div class="loc-tile" role="img" aria-label="Photo of modern office towers in Beijing" style="background:linear-gradient(180deg,#9fb6cd,#4a4f55)"><span>Finibus Bonorum</span></div>
      </div>
      <div class="loc-side">
        <p>Sed ut perspiciatis unde omnis iste natusit voluptatem acc usantium doloremque laudantotam. Sed ut perspiciatis unde omnis iste natusit voluptatem accusantium doloremque laudan tiumtotam laudantotamtotam.</p>
        <div class="map" role="img" aria-label="Illustrated outline map of China with a flag"></div>
      </div>
    </div>
  </div>
</section>

<section class="how">
  <div class="wrap">
    <h2 class="section-title">How it <span>Works</span></h2>
    <div class="steps">
      <div class="step"><div class="circle"><svg width="36" height="36" viewBox="0 0 36 36"><path d="M8 28l2-8L24 6l6 6-14 14z" fill="#e2001a"/><path d="M8 28l2-8 6 6z" fill="#fff"/></svg></div><h3>1. Apply</h3><p>Sed ut perspiciatis unde omnisit iste natusit voluptatem accusantium dolorae laudantiumtotam accusantium.</p></div>
      <div class="step"><div class="circle"><svg width="38" height="36" viewBox="0 0 38 36"><ellipse cx="19" cy="16" rx="15" ry="11" fill="#e2001a"/><path d="M10 24l-3 8 10-6z" fill="#e2001a"/><circle cx="13" cy="16" r="1.8" fill="#fff"/><circle cx="19" cy="16" r="1.8" fill="#fff"/><circle cx="25" cy="16" r="1.8" fill="#fff"/></svg></div><h3>2. Interview</h3><p>Sed ut perspiciatis unde omnisit iste natusit voluptatem accusantium dolorae laudantiumtotam accusantium.</p></div>
      <div class="step"><div class="circle"><svg width="34" height="34" viewBox="0 0 34 34"><rect x="3" y="6" width="28" height="25" rx="2" fill="#e2001a"/><rect x="6" y="13" width="22" height="15" fill="#fff"/><rect x="9" y="2" width="3" height="7" fill="#e2001a"/><rect x="22" y="2" width="3" height="7" fill="#e2001a"/><rect x="9" y="16" width="4" height="4" fill="#e2001a"/></svg></div><h3>3. Start Work</h3><p>Sed ut perspiciatis unde omnisit iste natusit voluptatem accusantium dolorae laudantiumtotam accusantium.</p></div>
      <div class="step"><div class="circle"><svg width="36" height="32" viewBox="0 0 36 32"><path d="M18 30S3 20 3 10a7.5 7.5 0 0 1 15-2 7.5 7.5 0 0 1 15 2c0 10-15 20-15 20z" fill="#e2001a"/></svg></div><h3>4. Free Service</h3><p>Sed ut perspiciatis unde omnisit iste natusit voluptatem accusantium dolorae laudantiumtotam accusantium.</p></div>
    </div>
  </div>
</section>

<section class="blog">
  <div class="wrap">
    <h2 class="section-title">Recent Blog <span>Posts</span></h2>
    <div class="posts">
      <article class="post"><div class="thumb" role="img" aria-label="Photo of a fisherman on a river at sunset" style="background:linear-gradient(180deg,#c9a36a,#4b5a52)"></div><div><h3>Basic Chinese Greetings</h3><p>Chinese is a pretty difficult language for English speakers to learn compared to Spanish or French. However, if you're going to China, take the time …</p><div class="date"><svg width="9" height="9" viewBox="0 0 9 9"><rect x=".5" y="1.5" width="8" height="7" fill="none" stroke="#888"/></svg>Mar 24, 2017</div></div></article>
      <article class="post"><div class="thumb" role="img" aria-label="Photo of a traditional Chinese gate with red columns" style="background:linear-gradient(135deg,#3f6b8e,#a8332a)"></div><div><h3>How China Can Get..</h3><p>Chinese is a pretty difficult language for English speakers to learn compared to Spanish or French. However, if you're going to China, take the time …</p><div class="date"><svg width="9" height="9" viewBox="0 0 9 9"><rect x=".5" y="1.5" width="8" height="7" fill="none" stroke="#888"/></svg>Mar 24, 2017</div></div></article>
      <article class="post"><div class="thumb" role="img" aria-label="Photo of a temple roof framed by trees" style="background:linear-gradient(180deg,#6c8fb4,#7a3a2a)"></div><div><h3>TEFL TESOL Teach Jobs</h3><p>Chinese is a pretty difficult language for English speakers to learn compared to Spanish or French. However, if you're going to China, take the time …</p><div class="date"><svg width="9" height="9" viewBox="0 0 9 9"><rect x=".5" y="1.5" width="8" height="7" fill="none" stroke="#888"/></svg>Mar 24, 2017</div></div></article>
      <article class="post"><div class="thumb" role="img" aria-label="Photo of a garden pavilion surrounded by greenery" style="background:linear-gradient(135deg,#4d7a3a,#9a5a3a)"></div><div><h3>What are ESOL,EFL,ESL</h3><p>Chinese is a pretty difficult language for English speakers to learn compared to Spanish or French. However, if you're going to China, take the time …</p><div class="date"><svg width="9" height="9" viewBox="0 0 9 9"><rect x=".5" y="1.5" width="8" height="7" fill="none" stroke="#888"/></svg>Mar 24, 2017</div></div></article>
    </div>
  </div>
</section>

<section class="banner" role="img" aria-label="Photo of a smiling teacher in an office, blurred background">
  <div class="wrap">
    <h2>TEFL TESOL Teach Jobs</h2>
    <p>Sed ut perspiciatis unde omnis iste natusit volupta tem accusantium doloremque laudantotam.</p>
    <span class="btn">View Job Board</span>
  </div>
</section>

<footer class="footer">
  <div class="wrap">
    <div class="f-cols">
      <div><h4>Popular Locations</h4><ul><li>Jobs Abroad</li><li>Jobs in China</li><li>Jobs in Shanghai</li><li>Jobs in Beijing</li><li>Jobs in Shenzhen</li><li>Jobs in Guangzhou</li></ul></div>
      <div><h4>Featured Jobs</h4><ul><li>Harbor Street China</li><li>Harbor Street Vietnam</li><li>First Step English</li><li>Little Tower Shanghai</li><li>Blue Heron English</li><li>Language School Fuzhou</li><li>Intl. Schools in Saudi</li></ul></div>
      <div><h4>Types of Jobs</h4><ul><li>Kindergarten Jobs</li><li>Language School Jobs</li><li>Public Schools Jobs</li><li>University Jobs</li><li>Adult Student Jobs</li><li>Business English Jobs</li></ul></div>
      <div class="contact"><h4>Contact</h4><ul>
        <li><svg width="9" height="11" viewBox="0 0 9 11"><path d="M4.5 11S0 6 0 4.5a4.5 4.5 0 0 1 9 0C9 6 4.5 11 4.5 11z" fill="#888"/></svg><span>For questions contact<br>Marla Greene, Director<br>418 Willow Bend Rd<br>Riverton, Ohio 45012</span></li>
        <li><svg width="10" height="10" viewBox="0 0 10 10"><path d="M2 0l2 2.5-1.2 1.5a6 6 0 0 0 3.2 3.2L7.5 6 10 8l-1.5 2C4 10 0 6 0 1.5z" fill="#888"/></svg><span>Phone: 555 014 2290</span></li>
        <li><svg width="11" height="9" viewBox="0 0 11 9"><rect x=".5" y=".5" width="10" height="8" fill="none" stroke="#888"/><path d="M.5.5l5 4 5-4" fill="none" stroke="#888"/></svg><span>Email: Marla@BrightLanternPost.com</span></li>
      </ul></div>
    </div>
  </div>
  <div class="live-chat">LIVE CHAT</div>
  <div class="f-bottom">
    <div class="wrap">
      <span>Copyright © 2017 All Copyrights reserved Bright Lantern Post.</span>
      <span class="brand">Bright Lantern Post</span>
    </div>
  </div>
</footer>

</body>
</html>
```